Residential Remodeling Contractor needs updated business card

I need a new design for my business card.
Name of the company is Ridgefell Construction. I need a card that commands presence, strength, integrity. I have been in business for 28 years. I am a Residential Remodeling Contractor that covers all aspects of a residential remodel and build.

```html
<!DOCTYPE html>
<html lang="en">
<head>
<meta charset="utf-8">
<title>Ridgefell Construction — Business Card</title>
<link rel="stylesheet" href="https://fonts.googleapis.com/css2?family=Libre+Baskerville:wght@400;700&family=Arimo:wght@400&display=swap">
<style>
  :root {
    --stage: #1f2022;
    --card-blue: #1a4488;
    --card-blue-deep: #143a78;
    --ink: #ffffff;
    --ink-soft: rgba(255,255,255,0.85);
    --rule: rgba(255,255,255,0.75);
  }
  * { margin: 0; padding: 0; box-sizing: border-box; }
  html, body { width: 1200px; height: 801px; overflow: hidden; }
  body {
    background: var(--stage);
    display: flex;
    align-items: center;
    justify-content: center;
    gap: 44px;
  }
  .card {
    position: relative;
    width: 520px;
    height: 300px;
    border-radius: 22px;
    background: linear-gradient(160deg, var(--card-blue) 0%, var(--card-blue-deep) 100%);
    color: var(--ink);
    overflow: hidden;
  }

  /* Brand name: plain text with a plain square marking the symbol's place */
  .brand {
    display: flex;
    align-items: center;
  }
  .brand-mark {
    flex: none;
    background: var(--ink);
  }
  .brand-name {
    font-family: "Libre Baskerville", serif;
    font-weight: 400;
    color: var(--ink);
    line-height: 1.2;
  }
  .brand-name .line { display: block; }

  /* Details side */
  .card-front .brand {
    position: absolute;
    top: 30px;
    right: 36px;
    gap: 12px;
  }
  .card-front .brand-mark { width: 34px; height: 34px; }
  .card-front .brand-name { font-size: 19px; }

  .holder {
    position: absolute;
    left: 36px;
    top: 134px;
  }
  .holder-name {
    font-family: "Libre Baskerville", serif;
    font-weight: 700;
    font-size: 18px;
    letter-spacing: 0.03em;
    text-transform: uppercase;
  }
  .holder-title {
    font-family: "Arimo", sans-serif;
    font-size: 12px;
    color: var(--ink-soft);
    margin-top: 4px;
  }
  .contacts {
    list-style: none;
    position: absolute;
    left: 36px;
    top: 190px;
    font-family: "Arimo", sans-serif;
    font-size: 12px;
  }
  .contacts li {
    display: flex;
    align-items: center;
    gap: 8px;
    height: 17px;
  }
  .contacts svg { width: 10px; height: 10px; fill: var(--ink); flex: none; }
  .rule {
    position: absolute;
    left: 36px;
    right: 36px;
    top: 252px;
    height: 1px;
    background: var(--rule);
  }
  .address {
    position: absolute;
    left: 36px;
    top: 264px;
    font-family: "Arimo", sans-serif;
    font-size: 11.5px;
    letter-spacing: 0.02em;
    color: var(--ink-soft);
  }

  /* Brand side */
  .card-back {
    display: flex;
    align-items: center;
    justify-content: center;
  }
  .card-back .brand { gap: 20px; }
  .card-back .brand-mark { width: 64px; height: 64px; }
  .card-back .brand-name { font-size: 34px; }
</style>
</head>
<body>

  <section class="card card-front" aria-label="Business card, details side">
    <div class="brand">
      <span class="brand-mark" aria-hidden="true"></span>
      <div class="brand-name">
        <span class="line">Ridgefell</span>
        <span class="line">Construction</span>
      </div>
    </div>

    <div class="holder">
      <div class="holder-name">Daniel Ostrander</div>
      <div class="holder-title">Owner &amp; Manager</div>
    </div>

    <ul class="contacts">
      <li>
        <svg viewBox="0 0 10 10" aria-hidden="true"><path d="M2 0.5l1.8 2-1 1.2c.6 1.3 1.5 2.2 2.6 2.7l1.1-1 2 1.7-1 2.2C4.2 9 1 5.8 0.6 1.6z"/></svg>
        <span>555 014 2290</span>
      </li>
      <li>
        <svg viewBox="0 0 10 10" aria-hidden="true"><path d="M0 2h10v6H0z M0.8 2.6 5 5.6l4.2-3" stroke="#1a4488" stroke-width="0.8"/></svg>
        <span>info@ridgefellconstruction.com</span>
      </li>
      <li>
        <svg viewBox="0 0 10 10" aria-hidden="true"><circle cx="5" cy="5" r="4.6"/><path d="M0.6 5h8.8M5 0.4c-2.4 2.6-2.4 6.6 0 9.2M5 0.4c2.4 2.6 2.4 6.6 0 9.2" stroke="#1a4488" stroke-width="0.7" fill="none"/></svg>
        <span>www.ridgefellconstruction.com</span>
      </li>
    </ul>

    <div class="rule"></div>
    <p class="address">P.O. Box&nbsp; Street Name Country Name AB, A5B 521</p>
  </section>

  <section class="card card-back" aria-label="Business card, brand side">
    <div class="brand">
      <span class="brand-mark" aria-hidden="true"></span>
      <div class="brand-name">
        <span class="line">Ridgefell</span>
        <span class="line">Construction</span>
      </div>
    </div>
  </section>

</body>
</html>
```